Website for International Non-Profit for Birth Parent Searching

LumaKin is a 501(c)(3) non-profit organization that helps Chinese adoptees search and reunite with birth families who were separated due the One Child Policy in China. We want to create a website that can link to an information database that allows website users to easily access information around search ads in an organized way; help connect families to professional searchers; provide resources for community support for adoptees and their families as they embark on a personal and emotional journey of finding birth family through support groups on social media and consultation/education on the searching process; and provide the opportunity for the adoptive community to give back through donations and volunteer opportunities. The final design should foster a sense of community and be easy navigable to access the multiple resources we provide to help families search for each other. We would like to see designs with red/black/white color schemes that are gentle, inviting, and family friendly to viewers. We would like to see some design layouts with Chinese themes, if possible.

```html
<!DOCTYPE html>
<html lang="en">
<head>
<meta charset="utf-8">
<title>LumaKin — International Non-Profit for Birth Parent Searching</title>
<link rel="stylesheet" href="https://fonts.googleapis.com/css2?family=Lato:wght@400;700;900&family=Open+Sans:wght@400;600;700&display=swap">
<style>
:root{
  --red:#b3121d;
  --red-dark:#8c0d15;
  --black:#111111;
  --ink:#2b2b2b;
  --muted:#6d6d6d;
  --line:#d9d9d9;
  --grey-bg:#eeeeee;
  --pink-bg:#f6e3e3;
  --white:#ffffff;
}
*{box-sizing:border-box;margin:0;padding:0}
html,body{width:1200px;height:5376px;overflow:hidden}
body{position:relative;background:var(--white);font-family:"Open Sans",Arial,sans-serif;color:var(--ink)}
.abs{position:absolute}
h1,h2,h3,.nav,.btn{font-family:"Lato",Helvetica,sans-serif}
.btn{display:inline-block;font-size:15px;font-weight:700;letter-spacing:.5px;text-transform:uppercase;padding:12px 26px;border-radius:3px;text-align:center}
.btn-red{background:var(--red);color:var(--white)}
.btn-white{background:var(--white);color:var(--black)}
.btn-outline{border:2px solid var(--red);color:var(--red);background:var(--white);border-radius:22px;padding:8px 22px;font-size:13px}
.section-title{font-size:42px;font-weight:900;text-transform:uppercase;text-align:center;color:var(--black);letter-spacing:.5px}
.section-title .accent{color:var(--red)}

/* Header */
.site-header{left:0;top:0;width:1200px;height:64px;background:var(--white);z-index:5}
.brand{left:0;top:0;width:220px;height:130px;background:var(--white);border-radius:0 0 60px 0;z-index:6;display:flex;align-items:center;gap:12px;padding-left:30px}
.brand-dot{width:40px;height:40px;border-radius:50%;background:var(--red)}
.brand-name{font-family:"Lato",sans-serif;font-weight:900;font-size:30px;color:var(--red)}
.nav{left:270px;top:0;height:64px;display:flex;align-items:center;gap:34px;font-size:15px;font-weight:700;text-transform:uppercase;color:var(--black)}
.nav .active{color:var(--red);border-bottom:3px solid var(--red);padding-bottom:6px}
.nav .donate{background:var(--red);color:var(--white);padding:10px 20px;border-radius:3px}

/* Hero */
.hero-photo{left:0;top:0;width:1200px;height:800px;background:linear-gradient(110deg,#2c4a2a 0%,#5e7d44 35%,#a8b98a 60%,#d9c9b2 80%,#7f8f5a 100%)}
.hero-shade{left:0;top:0;width:700px;height:800px;background:linear-gradient(90deg,rgba(0,0,0,.45),rgba(0,0,0,0))}
.hero-title{left:60px;top:150px;width:560px;font-size:54px;line-height:62px;font-weight:900;color:var(--white)}
.hero-actions{left:140px;top:468px;display:flex;gap:24px}
.hero-curve{left:0;top:690px;width:1200px;height:130px}

/* Pillars */
.pillar{border-radius:50%;background:#ececec;display:flex;flex-direction:column;align-items:center;text-align:center;box-shadow:0 6px 18px rgba(0,0,0,.18)}
.pillar h3{font-size:17px;font-weight:900;text-transform:uppercase;margin-top:10px}
.pillar p{font-size:12px;line-height:17px;color:var(--muted);width:170px;margin-top:8px}
.pillar .arrow{margin-top:12px}
.pillar-side{width:250px;height:250px;top:600px;padding-top:40px}
.pillar-main{left:455px;top:560px;width:290px;height:290px;background:var(--red);color:var(--white);padding-top:46px}
.pillar-main p{color:#f3d6d6;width:200px}
.pillar-main .btn-outline{margin-top:14px;background:transparent;border-color:var(--white);color:var(--white)}

/* Welcome */
.welcome{left:0;top:960px;width:1200px;text-align:center}
.welcome p{width:840px;margin:26px auto 0;font-size:14px;line-height:22px;color:var(--muted)}
.welcome .btn{margin-top:28px}

/* Services */
.services{left:0;top:1400px;width:1200px;height:528px;background:var(--grey-bg)}
.services .section-title{margin-top:56px}
.service{top:150px;width:260px;text-align:center}
.service-icon{width:110px;height:110px;margin:0 auto}
.service h3{font-size:16px;font-weight:900;text-transform:uppercase;margin-top:14px}
.service p{font-size:13px;line-height:19px;color:var(--muted);margin-top:8px}
.service .btn-outline{margin-top:18px}
.carousel-arrow{font-family:"Lato",sans-serif;font-size:44px;color:#9a9a9a}

/* Birth parent searching */
.search-photo{left:0;top:1928px;width:1200px;height:552px;background:linear-gradient(100deg,#3e5a2c 0%,#6f8a4c 40%,#a9b27a 65%,#577236 100%)}
.search-card{left:680px;top:2036px;width:440px;height:340px;background:var(--white);padding:34px 28px}
.search-card h2{font-size:32px;line-height:36px;font-weight:900;text-transform:uppercase;color:var(--black)}
.search-card p{font-size:13px;line-height:20px;color:var(--muted);margin-top:14px}
.search-card .btn{margin-top:20px;font-size:13px;padding:10px 20px}

/* Action grid */
.action{left:0;top:2480px;width:1200px}
.action .section-title{margin-top:56px}
.action-card{width:440px}
.action-card .photo{height:300px}
.action-card .label{height:58px;background:var(--red);color:var(--white);font-family:"Lato",sans-serif;font-weight:900;font-size:17px;text-transform:uppercase;display:flex;align-items:center;justify-content:center;letter-spacing:.5px}

/* Testimonials */
.testimonials{left:0;top:3440px;width:1200px;height:560px}
.testimonials .section-title{margin-top:60px}
.quote{top:3600px;width:410px;height:230px;background:var(--white);border-radius:8px;box-shadow:0 4px 16px rgba(0,0,0,.15);padding:30px 30px}
.quote .mark{font-family:"Lato",sans-serif;font-size:60px;line-height:30px;color:var(--red);font-weight:900}
.quote p{font-size:13px;line-height:20px;color:var(--muted);margin-top:-8px}
.stars{margin-top:12px;color:#e3a21a;font-size:16px;letter-spacing:2px}
.author{top:3866px;display:flex;align-items:center;gap:14px}
.avatar{width:58px;height:58px;border-radius:50%;background:linear-gradient(135deg,#c9a98a,#7a5a44);border:3px solid var(--white);box-shadow:0 2px 6px rgba(0,0,0,.2)}
.author .name{font-size:12px;font-weight:700;line-height:17px;text-transform:uppercase;color:var(--black)}

/* Newsletter */
.newsletter{left:0;top:3990px;width:1200px;height:470px}
.newsletter-bg{left:0;top:0;width:1200px;height:470px;background:linear-gradient(90deg,#7d0a11 0%,#a3121c 40%,#b8323a 60%,#8a0d15 100%)}
.newsletter h2{left:0;top:150px;width:1200px;text-align:center;font-size:34px;font-weight:900;color:var(--white);text-transform:uppercase}
.field-dark{height:44px;border:1px solid rgba(255,255,255,.7);color:#f1d5d5;font-size:13px;padding:12px 14px;background:rgba(0,0,0,.1)}
.newsletter .btn{top:300px;left:810px;width:160px;height:44px;padding:12px 0}

/* Contact */
.contact{left:0;top:4460px;width:1200px;height:620px;background:var(--pink-bg)}
.contact .section-title{margin-top:60px}
.field{background:var(--white);border:1px solid var(--line);height:44px;font-size:13px;color:var(--muted);padding:12px 14px}

/* Footer */
.site-footer{left:0;top:5080px;width:1200px;height:296px;background:var(--black);color:var(--white)}
.footer-brand{left:50px;top:60px;display:flex;align-items:center;gap:12px}
.footer-brand .brand-name{color:var(--white)}
.footer-nav{left:360px;top:94px;display:flex;gap:40px;font-family:"Lato",sans-serif;font-size:14px;font-weight:700;text-transform:uppercase}
.footer-line{left:360px;top:132px;width:780px;height:1px;background:#444}
.footer-contact{left:360px;top:156px;display:flex;gap:60px;font-size:14px;align-items:center}
.footer-contact span{display:flex;align-items:center;gap:12px}
.footer-contact .ico{width:34px;height:34px;background:var(--red);display:flex;align-items:center;justify-content:center;border-radius:3px}
.footer-copy{left:360px;top:224px;font-size:12px;color:#aaa;text-transform:uppercase;letter-spacing:.5px}
</style>
</head>
<body>

<!-- Hero -->
<div class="abs hero-photo" role="img" aria-label="Photo of a smiling father and mother with their young child outdoors among green trees"></div>
<div class="abs hero-shade"></div>

<header class="abs site-header"></header>
<div class="abs brand"><span class="brand-dot"></span><span class="brand-name">LumaKin</span></div>
<nav class="abs nav">
  <span class="active">Home</span>
  <span>Who we are ▾</span>
  <span>Our services</span>
  <span>Get involved</span>
  <span>Tools and resources</span>
  <span class="donate">Donate now</span>
  <span>EN ▾</span>
</nav>

<h1 class="abs hero-title">International Non-Profit for Birth Parent Searching</h1>
<div class="abs hero-actions">
  <span class="btn btn-white">Search ads</span>
  <span class="btn btn-red">Connect</span>
</div>

<svg class="abs hero-curve" viewBox="0 0 1200 130" preserveAspectRatio="none">
  <path d="M0 70 C300 20 500 120 800 70 C1000 35 1120 40 1200 50 L1200 130 L0 130 Z" fill="#ffffff"/>
  <path d="M0 70 C300 20 500 120 800 70 C1000 35 1120 40 1200 50" fill="none" stroke="#b3121d" stroke-width="6"/>
</svg>

<!-- Pillars -->
<div class="abs pillar pillar-side" style="left:155px">
  <svg width="46" height="46" viewBox="0 0 46 46"><rect x="6" y="6" width="34" height="34" fill="none" stroke="#b3121d" stroke-width="3"/><path d="M14 28 l8-8 6 6 8-10" fill="none" stroke="#b3121d" stroke-width="3"/></svg>
  <h3>Mission</h3>
  <p>Sed ut perspiciatis unde omnis iste natus error sit voluptatem accusantium doloremque laudantium.</p>
  <svg class="arrow" width="22" height="14" viewBox="0 0 22 14"><path d="M0 7h19M13 1l6 6-6 6" fill="none" stroke="#111" stroke-width="2"/></svg>
</div>
<div class="abs pillar pillar-main">
  <svg width="50" height="46" viewBox="0 0 50 46"><path d="M4 30 l12-12 10 6 20-14" fill="none" stroke="#fff" stroke-width="3"/><circle cx="25" cy="10" r="6" fill="none" stroke="#fff" stroke-width="3"/><path d="M6 40h38" stroke="#fff" stroke-width="3"/></svg>
  <h3>Donations</h3>
  <p>Sed ut perspiciatis unde omnis iste natus voluptatem accusantium doloremque laudantium, totam rem aperiam, eaque ipsa.</p>
  <span class="btn btn-outline">Learn more</span>
</div>
<div class="abs pillar pillar-side" style="left:795px">
  <svg width="46" height="46" viewBox="0 0 46 46"><rect x="6" y="12" width="34" height="26" fill="none" stroke="#b3121d" stroke-width="3"/><circle cx="23" cy="25" r="6" fill="none" stroke="#b3121d" stroke-width="3"/><path d="M16 12l4-6h6l4 6" fill="none" stroke="#b3121d" stroke-width="3"/></svg>
  <h3>Vision</h3>
  <p>Sed ut perspiciatis unde omnis iste natus error sit voluptatem accusantium doloremque laudantium.</p>
  <svg class="arrow" width="22" height="14" viewBox="0 0 22 14"><path d="M0 7h19M13 1l6 6-6 6" fill="none" stroke="#111" stroke-width="2"/></svg>
</div>

<!-- Welcome -->
<section class="abs welcome">
  <h2 class="section-title">Welcome to LumaKin</h2>
  <p>Sed ut perspiciatis unde omnis iste natus error sit voluptatem accusantium doloremque laudantium, totam rem aperiam, eaque ipsa quae ab illo inventore veritatis et quasi architecto beatae vitae dicta sunt explicabo. Nemo enim ipsam voluptatem quia voluptas sit aspernatur aut odit aut fugit, sed quia consequuntur magni dolores eos qui ratione voluptatem sequi nesciunt. Neque porro quisquam est, qui dolorem ipsum quia dolor sit amet, consectetur, adipisci velit, sed quia non numquam eius modi tempora incidunt ut labore et dolore magnam aliquam quaerat voluptatem. Ut enim ad minima veniam, quis nostrum exercitationem ullam.</p>
  <span class="btn btn-red">Meet us</span>
</section>

<!-- Services -->
<section class="abs services">
  <h2 class="section-title">Our services</h2>
  <span class="abs carousel-arrow" style="left:80px;top:250px">‹</span>
  <span class="abs carousel-arrow" style="left:1100px;top:250px">›</span>
  <div class="abs service" style="left:200px">
    <svg class="service-icon" viewBox="0 0 110 110"><path d="M55 5a50 50 0 1 0 50 50A38 38 0 1 1 55 5Z" fill="#b3121d"/><path d="M62 56l10-9 10 9v12H62Z" fill="none" stroke="#b3121d" stroke-width="3"/></svg>
    <h3>Finibus bonorum</h3>
    <p>Exercitation ullamco laboris nisi ut aliquip ex ea commodo consequat with more cillum dolore eu fugiat.</p>
    <span class="btn btn-outline">Learn more</span>
  </div>
  <div class="abs service" style="left:470px">
    <svg class="service-icon" viewBox="0 0 110 110"><path d="M55 5a50 50 0 1 0 50 50A38 38 0 1 1 55 5Z" fill="#b3121d"/><circle cx="70" cy="52" r="9" fill="none" stroke="#b3121d" stroke-width="3"/><path d="M63 59l-8 10" stroke="#b3121d" stroke-width="3"/></svg>
    <h3>Necessitatibus saepe</h3>
    <p>Exercitation ullamco laboris nisi ut aliquip ex ea commodo consequat with more cillum dolore eu fugiat.</p>
    <span class="btn btn-outline">Learn more</span>
  </div>
  <div class="abs service" style="left:740px">
    <svg class="service-icon" viewBox="0 0 110 110"><path d="M55 5a50 50 0 1 0 50 50A38 38 0 1 1 55 5Z" fill="#b3121d"/><circle cx="64" cy="48" r="5" fill="none" stroke="#b3121d" stroke-width="3"/><circle cx="78" cy="48" r="5" fill="none" stroke="#b3121d" stroke-width="3"/><path d="M56 68c0-8 16-8 16 0M70 68c0-8 16-8 16 0" fill="none" stroke="#b3121d" stroke-width="3"/></svg>
    <h3>Officia deserunt</h3>
    <p>Exercitation ullamco laboris nisi ut aliquip ex ea commodo consequat with more cillum dolore eu fugiat.</p>
    <span class="btn btn-outline">Learn more</span>
  </div>
</section>

<!-- Birth parent searching -->
<div class="abs search-photo" role="img" aria-label="Photo of a family with two children sitting together in a green park"></div>
<div class="abs search-card">
  <h2>Birth parent<br>searching</h2>
  <p>Sed ut perspiciatis unde omnis iste natus error sit voluptatem accusantium doloremque laudantium, totam rem aperiam, eaque ipsa quae ab illo inventore veritatis et quasi architecto beatae vitae dicta sunt explicabo. Nemo enim ipsam voluptatem quia voluptas sit aspernatur aut odit aut fugit, sed quia consequuntur.</p>
  <span class="btn btn-red">Start your search</span>
</div>

<!-- Get in on the action -->
<section class="abs action">
  <h2 class="section-title">Get in on the action</h2>
</section>
<div class="abs action-card" style="left:148px;top:2630px">
  <div class="photo" role="img" aria-label="Photo of a mother and daughter hugging outdoors" style="background:linear-gradient(135deg,#8fa46a,#c8b38c)"></div>
  <div class="label">Join the conversation</div>
</div>
<div class="abs action-card" style="left:612px;top:2630px">
  <div class="photo" role="img" aria-label="Photo of a family celebrating together in festive red clothing" style="background:linear-gradient(135deg,#9c2a2a,#d7b9a0)"></div>
  <div class="label">Upcoming events</div>
</div>
<div class="abs action-card" style="left:148px;top:3010px">
  <div class="photo" role="img" aria-label="Photo of a group of smiling volunteers in white shirts" style="background:linear-gradient(135deg,#c9ccbf,#7f8f6a)"></div>
  <div class="label">Volunteer opportunities</div>
</div>
<div class="abs action-card" style="left:612px;top:3010px">
  <div class="photo" role="img" aria-label="Photo of a multi-generation family walking through a park" style="background:linear-gradient(135deg,#6f8c4a,#b8c28e)"></div>
  <div class="label">Recent news</div>
</div>

<!-- Testimonials -->
<section class="abs testimonials">
  <h2 class="section-title">What our clients say!</h2>
  <span class="abs carousel-arrow" style="left:128px;top:240px;font-size:36px">‹</span>
  <span class="abs carousel-arrow" style="left:1050px;top:240px;font-size:36px">›</span>
</section>
<div class="abs quote" style="left:170px">
  <div class="mark">“</div>
  <p>Sed ut perspiciatis unde omnis iste natus error sit voluptatem accusantium doloremque laudantium, totam rem aperiam, eaque ipsa quae ab illo inventore veritatis et quasi architecto beatae vitae dicta sunt explicabo. Nemo enim ipsam voluptatem quia voluptas sit aspernatur aut odit aut fugit.</p>
  <div class="stars">★★★★★</div>
</div>
<div class="abs quote" style="left:620px">
  <div class="mark">“</div>
  <p>Sed ut perspiciatis unde omnis iste natus error sit voluptatem accusantium doloremque laudantium, totam rem aperiam, eaque ipsa quae ab illo inventore veritatis et quasi architecto beatae vitae dicta sunt explicabo. Nemo enim ipsam voluptatem quia voluptas sit aspernatur aut odit aut fugit.</p>
  <div class="stars">★★★★★</div>
</div>
<div class="abs author" style="left:230px"><span class="avatar" role="img" aria-label="Client portrait"></span><span class="name">Mei Lin<br>LumaKin</span></div>
<div class="abs author" style="left:680px"><span class="avatar" role="img" aria-label="Client portrait"></span><span class="name">Mei Lin<br>LumaKin</span></div>

<!-- Newsletter -->
<section class="abs newsletter">
  <div class="abs newsletter-bg" role="img" aria-label="Soft red-toned photo of a child's face"></div>
  <svg class="abs" style="left:0;top:0" width="1200" height="90" viewBox="0 0 1200 90" preserveAspectRatio="none">
    <path d="M0 0H1200V30C900 90 700 20 420 60C250 85 100 60 0 40Z" fill="#ffffff"/>
  </svg>
  <h2>Join the community! Get email updates</h2>
  <div class="abs field-dark" style="left:230px;top:240px;width:360px">First Name</div>
  <div class="abs field-dark" style="left:610px;top:240px;width:360px">Last Name</div>
  <div class="abs field-dark" style="left:230px;top:300px;width:560px">Email address</div>
  <span class="abs btn btn-white">Submit</span>
</section>

<!-- Contact -->
<section class="abs contact">
  <h2 class="section-title">Get <span class="accent">in touch</span></h2>
  <div class="abs field" style="left:460px;top:200px;width:250px">First Name</div>
  <div class="abs field" style="left:730px;top:200px;width:250px">Last Name</div>
  <div class="abs field" style="left:460px;top:262px;width:250px">Email address</div>
  <div class="abs field" style="left:730px;top:262px;width:250px">Address</div>
  <div class="abs field" style="left:460px;top:324px;width:520px">Phone number</div>
  <div class="abs field" style="left:460px;top:386px;width:520px;height:120px">Reason for Inquiry</div>
  <span class="abs btn btn-red" style="left:522px;top:540px;width:156px;border-radius:22px;padding:10px 0;font-size:13px">Submit</span>
</section>

<!-- Footer -->
<footer class="abs site-footer">
  <div class="abs footer-brand"><span class="brand-dot"></span><span class="brand-name">LumaKin</span></div>
  <nav class="abs footer-nav">
    <span>Home</span><span>Who we are</span><span>Our services</span><span>Get involved</span><span>Tools and resources</span><span>Contact us</span>
  </nav>
  <div class="abs footer-line"></div>
  <div class="abs footer-contact">
    <span><span class="ico"><svg width="16" height="16" viewBox="0 0 16 16"><path d="M3 1h3l1 4-2 1a9 9 0 0 0 5 5l1-2 4 1v3c0 1-1 2-2 2A13 13 0 0 1 1 3c0-1 1-2 2-2Z" fill="#fff"/></svg></span>555 010 2846</span>
    <span><span class="ico"><svg width="14" height="18" viewBox="0 0 14 18"><path d="M7 0a7 7 0 0 1 7 7c0 5-7 11-7 11S0 12 0 7a7 7 0 0 1 7-7Z" fill="#fff"/><circle cx="7" cy="7" r="2.5" fill="#b3121d"/></svg></span>88 Harbor Lane, Suite 4</span>
    <span><span class="ico"><svg width="18" height="14" viewBox="0 0 18 14"><rect x="1" y="1" width="16" height="12" fill="none" stroke="#fff" stroke-width="2"/><path d="M1 1l8 7 8-7" fill="none" stroke="#fff" stroke-width="2"/></svg></span>hello@lumakin.org</span>
  </div>
  <div class="abs footer-copy">© Copyright 2021 LumaKin &nbsp;|&nbsp; All rights reserved</div>
</footer>

</body>
</html>
```